Client Meeting and installation Email Follow up

I would like a follow-up email template created.
Currently, we do a lot of new construction builds and meet with clients about 6-3 months before they take possession of their new house. I want a follow-up email template to be sent after the homeowner takes possession of their house that enquires if the clients are happy about their new lighting, the service they received, and their customer service representative with Brightwell Lamps and Breezes. I have attached a few files of what our current marketing looks like.
Target Market(s)
Home Owners We have already met with
Industry/Entity Type
Residential lighting
Font styles to use
Other font styles liked:
- Alta Light, Playfair Display, Montserrat
Colors
Designer to choose colors to be used in the design.
Look and feel
Each slider illustrates characteristics of the customer's brand and the style your logo design should communicate.

```html
<!DOCTYPE html>
<html lang="en">
<head>
<meta charset="utf-8">
<title>Brightwell Lamps and Breezes – Follow Up Email</title>
<link rel="stylesheet" href="https://fonts.googleapis.com/css2?family=Mulish:wght@300;400;600;700;800&display=swap">
<style>
:root{
  --black:#000000;
  --white:#ffffff;
  --ink:#1a1a1a;
  --muted:#333333;
  --rule:#444444;
}
*{box-sizing:border-box;margin:0;padding:0}
html,body{width:1200px;height:3492px;overflow:hidden;background:var(--white)}
body{position:relative;font-family:"Mulish",sans-serif;color:var(--ink)}
.top-bar{position:absolute;left:0;top:0;width:1200px;height:160px;background:var(--black);display:flex;align-items:center;justify-content:center}
.brand{font-family:"Mulish",sans-serif;font-weight:600;color:var(--white);text-align:center;line-height:1.05;letter-spacing:2px}
.brand .line1{display:block;font-size:52px}
.brand .line2{display:block;font-size:34px;letter-spacing:3px}
.hero{position:absolute;left:0;top:160px;width:1200px;height:700px;background:linear-gradient(180deg,#ecebe7 0%,#d9d6cf 45%,#9a7a5a 70%,#5b4a3a 100%)}
.hero-glow{position:absolute;left:180px;top:100px;width:880px;height:760px;border-radius:50%;background:radial-gradient(circle,rgba(255,255,255,1) 0%,rgba(255,255,255,.95) 45%,rgba(255,255,255,0) 70%)}
.hero-copy{position:absolute;left:0;top:300px;width:1200px;text-align:center}
.hero-title{font-size:60px;line-height:1.2;color:var(--black)}
.hero-title strong{font-weight:800;display:block;letter-spacing:1px}
.hero-title span{font-weight:300;display:block}
.hero-contact{margin-top:36px;font-size:28px;line-height:1.9;color:var(--black)}
.products{position:absolute;left:0;top:2380px;width:1200px;height:560px;background:linear-gradient(180deg,#ffffff 0%,#f1f1f1 60%,#e4e4e4 100%)}
.letter{position:absolute;left:32px;top:840px;width:1144px;height:1608px;background:var(--white);border:2px solid var(--rule);padding:64px 56px 0 56px;font-size:26px;line-height:1.55;color:var(--muted);overflow:hidden}
.salutation{font-size:30px;color:var(--ink);margin-bottom:40px}
.letter p{margin-bottom:44px}
.feedback{border:2px solid var(--rule);padding:40px 48px 40px 48px;margin:0 0 56px 0}
.feedback h2{font-size:26px;font-weight:700;color:var(--ink);margin-bottom:20px}
.feedback p{margin-bottom:30px}
.feedback ul{list-style:none;margin-bottom:30px}
.feedback li{position:relative;padding-left:56px;margin-bottom:24px}
.feedback li::before{content:"";position:absolute;left:0;top:10px;width:22px;height:22px;border-radius:50%;background:var(--black)}
.feedback p:last-child{margin-bottom:0}
.cta{font-weight:700;color:var(--ink)}
.signoff{margin-bottom:20px!important}
.signature{line-height:1.4}
.footer{position:absolute;left:0;top:2940px;width:1200px;height:552px;background:var(--black);color:var(--white);text-align:center}
.footer .brand{position:absolute;left:0;top:84px;width:1200px}
.follow{position:absolute;left:0;top:290px;width:1200px;font-size:24px;font-weight:800;letter-spacing:1px}
.socials{position:absolute;left:0;top:346px;width:1200px;display:flex;justify-content:center;gap:20px}
.social{width:58px;height:58px;border:3px solid var(--white);border-radius:50%}
.copyright{position:absolute;left:0;top:470px;width:1200px;font-size:20px}
</style>
</head>
<body>
<header class="top-bar">
  <div class="brand"><span class="line1">BRIGHTWELL</span><span class="line2">LAMPS &amp; BREEZES</span></div>
</header>

<section class="hero" role="img" aria-label="Bright modern kitchen with a long wooden dining table and pendant lights">
  <div class="hero-glow"></div>
</section>
<div class="hero-copy">
  <h1 class="hero-title"><strong>RESIDENTIAL</strong><span>LIGHTING AND</span><span>INSTALLATION</span></h1>
  <div class="hero-contact">Email : info@brightwelllamps.net<br>TEL: 403-555-0187</div>
</div>

<div class="products" role="img" aria-label="Row of pendant lights and a chandelier on a white background"></div>

<main class="letter">
  <div class="salutation">Dear [Client's Name],</div>
  <p>I hope you're settling in well and enjoying your new home! It's been [time since possession] since you took possession of your new house, and we at Brightwell Lamps and Breezes wanted to take a moment to follow up with you.</p>
  <section class="feedback">
    <h2>We'd love to know how you're finding your new lighting.</h2>
    <p>We take great pride in our products and services, and your feedback is invaluable in helping us maintain our high standards. Here are a few things we'd appreciate your thoughts on:</p>
    <ul>
      <li>Are you happy with the lighting in your new home?</li>
      <li>How would you rate the service you received from our team?</li>
      <li>Did our customer service representative meet your expectations?</li>
    </ul>
    <p>Your satisfaction is our top priority, so if there's anything that didn't meet your expectations, please let us know. We're here to make sure everything is just right.</p>
  </section>
  <p class="cta">A simple reply to this email is all it takes, or if you'd prefer, we can arrange a time to chat over the phone.</p>
  <p>Thank you again for choosing Brightwell Lamps and Breezes. We look forward to your feedback and hope to continue serving you in the future!</p>
  <p class="signoff">Warm regards,</p>
  <div class="signature">Daniel Hartley<br>CEO<br>Brightwell Lamps and Breezes<br>Email : info@brightwelllamps.net<br>TEL: 403-555-0187</div>
</main>

<footer class="footer">
  <div class="brand"><span class="line1">BRIGHTWELL</span><span class="line2">LAMPS &amp; BREEZES</span></div>
  <div class="follow">FOLLOW US</div>
  <div class="socials">
    <span class="social"></span><span class="social"></span><span class="social"></span><span class="social"></span><span class="social"></span>
  </div>
  <div class="copyright">Copyright © 2024 All Rights Reserved</div>
</footer>
</body>
</html>
```